Looking for a cool & simple business-card-design for digital agency

Hi!

We are a web agency that offers Reputation Management, Vextor & Seo Services and software development. We like cool things, we like innovative styles.

We have uploaded our logo.

Project Deadline Extended Reason: Client does not want any designs with the colorful logo. Please send us submissions ONLY with the blac and white logo. What the client would like to see:1) Back of the card: is a silver logo on a black background2) front of the card with all the data, please use white background and black logo thank you Added Friday, May 8, 2015

Industry/Entity Type

Software

```html
<!DOCTYPE html>
<html lang="en">
<head>
<meta charset="utf-8">
<title>Nexaro AG – Business Card</title>
<link rel="stylesheet" href="https://fonts.googleapis.com/css2?family=Mulish:wght@400;700;800&display=swap">
<style>
  :root {
    --backdrop: #e4e4e6;
    --card-white: #f4f4f4;
    --card-black: #262626;
    --ink: #1e1e1e;
    --ink-soft: #3a3a3a;
    --silver: #e9e9e9;
    --band-purple: #8a2c8f;
    --band-magenta: #e6147f;
    --band-orange: #f0641e;
    --icon-green: #5cb82e;
    --icon-pink: #d8268a;
    --icon-orange: #f08a1c;
  }
  * { box-sizing: border-box; margin: 0; padding: 0; }
  html, body {
    width: 1200px; height: 789px; overflow: hidden;
    background: var(--backdrop);
    font-family: "Mulish", "Century Gothic", sans-serif;
  }
  .stage {
    position: relative; width: 1200px; height: 789px;
    display: flex; align-items: center; justify-content: center; gap: 60px;
  }
  .card {
    position: relative; width: 500px; height: 286px;
    box-shadow: 0 10px 28px rgba(0,0,0,.18);
    overflow: hidden;
  }
  /* back */
  .card--back { background: var(--card-black); display: flex; align-items: center; justify-content: center; }
  .brand { display: flex; align-items: center; gap: 12px; }
  .brand__mark { width: 26px; height: 26px; flex: none; }
  .brand__text { display: flex; flex-direction: column; }
  .brand__name { font-weight: 800; font-size: 30px; letter-spacing: 1px; line-height: 1; }
  .brand__tagline { font-size: 11px; letter-spacing: 4.6px; margin-top: 5px; text-transform: uppercase; }
  .card--back .brand__name,
  .card--back .brand__tagline { color: var(--silver); }
  .card--back .brand__mark { background: var(--silver); }
  /* front */
  .card--front { background: var(--card-white); color: var(--ink); }
  .holder { position: absolute; left: 40px; top: 38px; }
  .holder__name { font-weight: 700; font-size: 17px; letter-spacing: .5px; text-transform: uppercase; }
  .holder__role { font-size: 11.5px; color: var(--ink-soft); margin-top: 3px; }
  .contact { position: absolute; left: 40px; top: 112px; font-size: 12px; line-height: 18px; color: var(--ink-soft); list-style: none; }
  .contact__item { display: flex; align-items: center; gap: 7px; }
  .contact__item--address { padding-left: 0; }
  .contact__icon { width: 13px; height: 13px; flex: none; }
  .card--front .brand { position: absolute; right: 34px; top: 150px; gap: 10px; }
  .card--front .brand__name { font-size: 25px; color: var(--ink); }
  .card--front .brand__tagline { font-size: 9.5px; letter-spacing: 3.9px; color: var(--ink); }
  .card--front .brand__mark { width: 22px; height: 22px; background: var(--ink); }
  .accent-band {
    position: absolute; left: 0; right: 0; bottom: 0; height: 9px;
    background: linear-gradient(90deg, var(--band-purple) 0%, var(--band-magenta) 35%, var(--band-magenta) 82%, var(--band-orange) 88%, var(--band-orange) 100%);
  }
</style>
</head>
<body>
<main class="stage">
  <section class="card card--back" aria-label="Card back">
    <div class="brand">
      <span class="brand__mark"></span>
      <div class="brand__text">
        <span class="brand__name">NEXARO AG</span>
        <span class="brand__tagline">Digitale Strategien</span>
      </div>
    </div>
  </section>

  <section class="card card--front" aria-label="Card front">
    <div class="holder">
      <p class="holder__name">Jordan Hale</p>
      <p class="holder__role">Managing Director</p>
    </div>
    <ul class="contact">
      <li class="contact__item contact__item--address">18 Maple Court</li>
      <li class="contact__item contact__item--address">Fairview, CA 90215</li>
      <li class="contact__item">
        <svg class="contact__icon" viewBox="0 0 13 13" aria-hidden="true"><rect width="13" height="13" rx="2.5" fill="var(--icon-green)"/><path d="M4 3.2c.4-.3.8-.2 1 .2l.6 1.2c.2.3.1.6-.2.8l-.5.4c.4.9 1.1 1.6 2 2l.4-.5c.2-.3.5-.4.8-.2l1.2.6c.4.2.5.6.2 1l-.6.7c-.3.3-.8.4-1.2.2C5.8 9 4 7.2 3.1 5.3c-.2-.4-.1-.9.2-1.2z" fill="#fff"/></svg>
        +61 800-555-0142
      </li>
      <li class="contact__item">
        <svg class="contact__icon" viewBox="0 0 13 13" aria-hidden="true"><rect width="13" height="13" rx="2.5" fill="var(--icon-pink)"/><rect x="3" y="4" width="7" height="5" fill="none" stroke="#fff" stroke-width="1"/><path d="M3 4l3.5 3L10 4" fill="none" stroke="#fff" stroke-width="1"/></svg>
        info@nexaro.com
      </li>
      <li class="contact__item">
        <svg class="contact__icon" viewBox="0 0 13 13" aria-hidden="true"><rect width="13" height="13" rx="2.5" fill="var(--icon-orange)"/><circle cx="6.5" cy="6.5" r="3.4" fill="none" stroke="#fff" stroke-width="1"/><path d="M3.1 6.5h6.8M6.5 3.1c-1.4 1.8-1.4 5 0 6.8M6.5 3.1c1.4 1.8 1.4 5 0 6.8" fill="none" stroke="#fff" stroke-width=".8"/></svg>
        www.nexaro.com
      </li>
    </ul>
    <div class="brand">
      <span class="brand__mark"></span>
      <div class="brand__text">
        <span class="brand__name">NEXARO AG</span>
        <span class="brand__tagline">Digitale Strategien</span>
      </div>
    </div>
    <div class="accent-band"></div>
  </section>
</main>
</body>
</html>
```